US Recruiting Firm Needs Dynamic Tri-Fold Brochure

Need tri-fold professional brochure for HR recruiting and consulting firm based in the US.

Target Market(s)

Clients seeking administrative and human resources talent

Industry/Entity Type

Recruitment

Font styles to use
Sans Serif

Requirements
Should not have
• No weird shapes
• No heavy geometric shapes -- I prefer curvy lines
• Not a dark brochure

```html
<!DOCTYPE html>
<html lang="en">
<head>
<meta charset="utf-8">
<title>Recruiting Tri-Fold Brochure – Inside Spread</title>
<link href="https://fonts.googleapis.com/css2?family=Montserrat:wght@500;600;700&family=Questrial&display=swap" rel="stylesheet">
<style>
  :root{
    --navy:#1d3a5f;
    --navy-deep:#0f2540;
    --purple:#9b2a8a;
    --green:#8cc63f;
    --orange:#f08a1c;
    --paper:#f4f5f6;
    --ink:#2f3a45;
    --stage:#d9dcdf;
  }
  *{box-sizing:border-box;margin:0;padding:0}
  html,body{width:1200px;height:800px;overflow:hidden;background:var(--stage)}
  body{font-family:"Questrial",sans-serif;color:var(--ink)}
  .spread{position:absolute;left:121px;top:30px;width:957px;height:740px;background:var(--paper);box-shadow:0 6px 24px rgba(0,0,0,.18);overflow:hidden}
  .panel{position:absolute;top:0;width:319px;height:740px}
  .panel--left{left:0}
  .panel--middle{left:319px}
  .panel--right{left:638px}
  .fold{position:absolute;top:0;width:24px;height:740px;background:linear-gradient(90deg,rgba(0,0,0,.06),rgba(0,0,0,0));pointer-events:none}
  .heading{font-family:"Montserrat",sans-serif;font-weight:600;color:var(--navy);text-transform:uppercase;font-size:19px;line-height:1.15;letter-spacing:.3px}
  .heading--compact{font-size:16.5px;line-height:1.2}
  .rule{display:block;height:2px;margin:8px 0 14px;background:linear-gradient(90deg,var(--purple),rgba(155,42,138,.2))}
  .copy{font-size:11.5px;line-height:1.5;color:var(--ink)}
  .ticks{list-style:none}
  .ticks li{position:relative;padding-left:20px;font-size:12.5px;line-height:1.7}
  .ticks li::before{content:"";position:absolute;left:2px;top:5px;width:5px;height:9px;border:solid var(--orange);border-width:0 2px 2px 0;transform:rotate(40deg)}
  .ticks--small li{font-size:11.5px;line-height:1.58}
  .ticks--light li{color:#fff;font-size:11px;line-height:1.5}
  .photo{position:absolute;border-radius:2px}
  .photo--presenter{left:0;top:470px;width:319px;height:200px;background:linear-gradient(135deg,#dfe3e8,#b9c0c8 45%,#8a7c6e 80%,#d8c6a6)}
  .photo--handshake{left:30px;top:235px;width:275px;height:160px;background:linear-gradient(135deg,#e9ecef,#7f8892 50%,#3b4450)}
  .left-inner{position:absolute;left:34px;top:48px;width:260px}
  .middle-inner{position:absolute;left:30px;top:48px;width:270px}
  .right-inner{position:absolute;left:22px;top:40px;width:280px}
  .why{margin-top:26px}
  .talent{position:absolute;left:339px;top:408px;width:598px;height:260px;background:linear-gradient(120deg,var(--navy-deep),var(--navy) 55%,#2c5680);padding:18px 24px}
  .talent .heading{color:#fff;font-size:15px;line-height:1.3}
  .talent-lists{display:flex;gap:40px;margin-top:12px}
  .talent-lists ul{width:250px}
  .footer{position:absolute;left:0;bottom:0;width:957px;height:80px}
  .url{position:absolute;bottom:16px;width:319px;text-align:center;font-family:"Montserrat",sans-serif;font-weight:500;font-size:14px;color:var(--navy);letter-spacing:.3px}
  .url--left{left:0}
  .url--middle{left:319px}
  .url--right{left:638px}
</style>
</head>
<body>
<main class="spread">
  <section class="panel panel--left">
    <div class="left-inner">
      <h2 class="heading">A Trusted<br>Recruiting Partner</h2>
      <span class="rule"></span>
      <p class="copy">We have over 20 years of recruiting and human resources experience. Our recruiters have the expertise, insights, and passion to bring value-added recruiting services to your company. We have a track record of excellence.</p>
      <h2 class="heading why">Why Choose Us?</h2>
      <span class="rule"></span>
      <ul class="ticks">
        <li>Dedicated to admin &amp; HR recruiting</li>
        <li>Highly qualified talent network</li>
        <li>Comprehensive pre-screening</li>
        <li>Simplified recruiting process</li>
        <li>Reasonable placement fees</li>
        <li>90-day replacement guarantee</li>
      </ul>
    </div>
    <div class="photo photo--presenter" role="img" aria-label="Photo of a presenter leading a meeting with seated colleagues"></div>
  </section>

  <section class="panel panel--middle">
    <div class="middle-inner">
      <h2 class="heading">Our Mission</h2>
      <span class="rule"></span>
      <p class="copy">We have a two-fold mission. We help companies hire the best administrative and human resources staff to help meet organizational goals and cultivate a highly engaged, productive workforce. We also help job seekers find fulfilling employment with awesome companies.</p>
    </div>
    <div class="photo photo--handshake" role="img" aria-label="Photo of business people shaking hands across a meeting table"></div>
  </section>

  <section class="panel panel--right">
    <div class="right-inner">
      <h2 class="heading heading--compact">We Provide Customized<br>Recruiting and Consulting<br>Services.</h2>
      <span class="rule"></span>
      <ul class="ticks ticks--small">
        <li>Requisition management</li>
        <li>Position &amp; candidate profiling</li>
        <li>Sourcing resumes</li>
        <li>Writing and placing job postings</li>
        <li>Screening &amp; interviewing candidates</li>
        <li>Shortlisting candidates</li>
        <li>Candidate assessment</li>
        <li>Coordinating interviews &amp; debriefing</li>
        <li>Candidate dispositioning &amp; updates</li>
        <li>Applicant tracking</li>
        <li>Job offer &amp; salary negotiation</li>
        <li>Offer letter &amp; new hire paperwork</li>
        <li>Due Diligence</li>
        <li>New hire check-in surveys</li>
      </ul>
    </div>
  </section>

  <section class="talent" aria-label="Positions">
    <h2 class="heading">We offer stellar administrative and HR talent. Positions<br>that we fill include:</h2>
    <div class="talent-lists">
      <ul class="ticks ticks--light">
        <li>HR Assistant</li>
        <li>HR Coordinator</li>
        <li>Recruiting Coordinator</li>
        <li>HR Specialist</li>
        <li>HR Generalist</li>
        <li>HR Consultant</li>
        <li>HR Manager</li>
        <li>HR Director</li>
        <li>Employee Relations</li>
      </ul>
      <ul class="ticks ticks--light">
        <li>Talent Acquisition Consultant</li>
        <li>Recruiter</li>
        <li>Benefits Specialist</li>
        <li>Compensation Specialist</li>
        <li>Training Specialist</li>
        <li>Learning &amp; Development Consultant</li>
        <li>Diversity &amp; Inclusion Consultant</li>
        <li>Administrative Assistant</li>
        <li>Executive Assistant</li>
        <li>Office Manager</li>
      </ul>
    </div>
  </section>

  <svg class="footer" viewBox="0 0 957 80" preserveAspectRatio="none" aria-hidden="true">
    <path d="M0 22 C120 8 220 8 319 20 C430 34 540 6 638 18 C750 32 860 6 957 16 V80 H0 Z" fill="var(--green)"/>
    <path d="M0 22 C120 8 220 8 319 20 C430 34 540 6 638 18 C750 32 860 6 957 16 V26 C860 16 750 42 638 28 C540 16 430 44 319 30 C220 18 120 18 0 32 Z" fill="var(--paper)"/>
    <path d="M0 18 C120 4 220 4 319 16 C430 30 540 2 638 14 C750 28 860 2 957 12" fill="none" stroke="var(--purple)" stroke-width="2.5"/>
  </svg>
  <p class="url url--left">www.recruitingfirm.example</p>
  <p class="url url--middle">www.recruitingfirm.example</p>
  <p class="url url--right">www.recruitingfirm.example</p>

  <div class="fold" style="left:319px"></div>
  <div class="fold" style="left:638px"></div>
</main>
</body>
</html>
```